Fun Employee News and Engagement Portal - Tidy Hearth Company

We are looking for a clean, but fun WordPress template for an internal employee engagement website. The site will be a place we share news, fun stories and pictures. We'll provide space for our employees to post comments, etc.
We are a deep dish pizza restaurant with a rich history. I'd love to see your take on a look and feel for us! The site will be called Bim-Zee. I've posted some images and colors along with this brief description.
Focus on making the template whimsical and fun! (Extra point for focusing on the "Lettering in lights" ).
I will continue to post additional pieces of art and content examples.
Reason: Our team is continuing to review designs. We've decided to extend the timing a few more days. Good luck! Make it playful!
Reason: We need more time with our team to review these designs. We are going to extend one more time!
Reason: Still trying to get enough time to review with the Bim-Zee team!
Reason: We are continuing to evaluate designs. Thank you!
Industry/Entity Type
American Restaurant
Number of Pages Required
1 page
Look and feel
Each slider illustrates characteristics of the customer's brand and the style your logo design should communicate.

```html
<!DOCTYPE html>
<html lang="en">
<head>
<meta charset="utf-8">
<title>Bim-Zee — Tidy Hearth Company</title>
<link href="https://fonts.googleapis.com/css2?family=Roboto+Slab:wght@400;700;800&family=Open+Sans:wght@400;600&display=swap" rel="stylesheet">
<style>
:root{
  --red:#e3262c;
  --red-dark:#c81d23;
  --paper:#eeeae0;
  --paper-line:#e6e1d5;
  --ink:#1f1f1f;
  --muted:#5a5650;
  --star:#f29a1f;
  --white:#ffffff;
}
*{box-sizing:border-box;margin:0;padding:0}
html,body{width:1200px;height:3659px;overflow:hidden}
body{background:var(--paper);font-family:"Open Sans",Arial,sans-serif;color:var(--ink);position:relative}
.slab{font-family:"Roboto Slab",Georgia,serif}
section,header,footer{position:absolute;left:0;width:1200px}
.btn{position:absolute;background:var(--red);color:var(--white);font-family:"Roboto Slab",Georgia,serif;font-weight:700;font-size:14px;letter-spacing:.3px;text-transform:uppercase;display:flex;align-items:center;justify-content:center;border-radius:2px}
.center-x{left:50%;transform:translateX(-50%)}

/* header */
.site-header{top:0;height:85px;background:var(--white)}
.brand{position:absolute;left:98px;top:20px;display:flex;align-items:center;gap:14px}
.brand-dot{width:46px;height:46px;border-radius:50%;background:var(--red)}
.brand-name{font-family:"Roboto Slab",Georgia,serif;font-weight:700;font-size:32px;color:var(--ink);letter-spacing:.5px}
.main-nav{position:absolute;left:380px;top:31px;display:flex;gap:0}
.main-nav a{font-family:"Roboto Slab",Georgia,serif;font-weight:700;font-size:13px;color:var(--ink);text-decoration:none;margin-right:50px}
.header-btn{left:935px;top:20px;width:168px;height:40px;font-size:12px}

/* hero */
.hero{top:85px;height:525px}
.hero-photo{position:absolute;inset:0;background:radial-gradient(ellipse at 50% 75%,#c9462f 0%,#8b3a25 30%,#3e3a2a 60%,#1f1b17 100%)}
.hero-shade{position:absolute;inset:0;background:rgba(0,0,0,.25)}
.hero-title{position:absolute;width:100%;top:180px;text-align:center;color:var(--white);font-family:"Roboto Slab",Georgia,serif;font-weight:700;font-size:46px}
.hero-sub{position:absolute;width:100%;top:240px;text-align:center;color:var(--white);font-family:"Roboto Slab",Georgia,serif;font-weight:400;font-size:27px}
.hero .btn{top:293px;width:200px;height:46px}
.slider-dots{position:absolute;top:501px;left:50%;transform:translateX(-50%);display:flex;gap:6px}
.slider-dots span{width:8px;height:8px;border-radius:50%;background:rgba(255,255,255,.5)}
.slider-dots span:first-child{background:var(--white)}

/* welcome */
.welcome{top:610px;height:560px}
.collage{position:absolute;left:110px;top:80px;width:397px;height:432px}
.tile{position:absolute}
.tile-a{left:0;top:0;width:192px;height:192px;background:linear-gradient(135deg,#b5552e,#7a4a2b)}
.tile-b{left:205px;top:0;width:192px;height:192px;background:linear-gradient(135deg,#9c6b3f,#c0452a)}
.tile-c{left:0;top:205px;width:192px;height:227px;background:linear-gradient(160deg,#8a5a36,#c4683a)}
.tile-d{left:205px;top:240px;width:192px;height:192px;background:linear-gradient(135deg,#a3502d,#6e4630)}
.welcome-copy{position:absolute;left:585px;top:118px;width:500px}
.welcome-copy h2{font-family:"Roboto Slab",Georgia,serif;font-weight:700;font-size:33px;margin-bottom:22px}
.welcome-copy p{font-size:12px;line-height:2.25;color:var(--muted);margin-bottom:28px}
.welcome .btn{left:587px;top:440px;width:150px;height:46px}

/* stories */
.section-title{position:absolute;width:100%;text-align:center;font-family:"Roboto Slab",Georgia,serif;font-weight:700;font-size:30px}
.section-sub{position:absolute;width:100%;text-align:center;font-size:13px;color:var(--muted)}
.card{position:absolute;width:236px}
.card-photo{height:226px}
.card-meta{display:flex;justify-content:space-between;align-items:center;margin-top:22px}
.card-title{font-family:"Roboto Slab",Georgia,serif;font-weight:700;font-size:12px}
.card-foot{display:flex;justify-content:space-between;align-items:center;margin-top:12px;font-size:11px;color:var(--muted)}
.comments{display:flex;align-items:center;gap:6px}
.stars{color:var(--star);font-size:13px;letter-spacing:1px}

.fun{top:1170px;height:606px}
.fun .section-title{top:40px}
.fun .section-sub{top:96px}
.fun .btn{top:513px;width:154px;height:46px}

/* menus */
.menus{top:1776px;height:436px}
.menus-photo{position:absolute;inset:0;background:linear-gradient(90deg,#5b4536,#7d6352 35%,#3b2f27 60%,#8a6f5a)}
.menus-shade{position:absolute;inset:0;background:rgba(0,0,0,.35)}
.menus .section-title{top:115px;color:var(--white)}
.menus-text{position:absolute;left:50%;transform:translateX(-50%);top:172px;width:820px;text-align:center;color:var(--white);font-size:14px;line-height:2.2}
.menus .btn{top:252px;width:246px;height:46px}

/* past stories */
.past{top:2212px;height:998px}
.past .section-title{top:72px}
.past .section-sub{top:128px}
.past .btn{top:858px;width:154px;height:46px}

/* partners */
.partners{top:3207px;height:203px}
.partner{position:absolute;top:0;height:130px;background:var(--white);border:1px solid #ddd6c6;display:flex;align-items:center;justify-content:center}
.badge{background:#cf3a32}

/* footer */
.site-footer{top:3410px;height:249px;background:var(--red);color:var(--white);text-align:center}
.footer-name{position:absolute;width:100%;top:38px;font-family:"Roboto Slab",Georgia,serif;font-weight:700;font-size:34px}
.footer-nav{position:absolute;width:100%;top:103px;display:flex;justify-content:center;gap:48px}
.footer-nav a{font-family:"Roboto Slab",Georgia,serif;font-weight:700;font-size:11px;color:var(--white);text-decoration:none}
.copyright{position:absolute;width:100%;top:137px;font-family:"Roboto Slab",Georgia,serif;font-weight:700;font-size:11px}
.social{position:absolute;top:172px;left:50%;transform:translateX(-50%);display:flex;gap:10px}
.social span{width:28px;height:28px;border-radius:50%;background:var(--white)}
</style>
</head>
<body>

<header class="site-header">
  <div class="brand"><span class="brand-dot"></span><span class="brand-name">BIM-ZEE</span></div>
  <nav class="main-nav">
    <a href="#">HOME</a><a href="#">ABOUT US</a><a href="#">BLOG</a><a href="#">FUN STORIES</a><a href="#">CONTACT US</a>
  </nav>
  <a class="btn header-btn">Post your comment</a>
</header>

<section class="hero">
  <div class="hero-photo" role="img" aria-label="Hands topping a fresh pizza with tomatoes, mozzarella and basil"></div>
  <div class="hero-shade"></div>
  <h1 class="hero-title">BIM-ZEE</h1>
  <p class="hero-sub">WE ARE A TIDY HEARTH COMPANY</p>
  <a class="btn center-x">Post your comment</a>
  <div class="slider-dots"><span></span><span></span><span></span><span></span></div>
</section>

<section class="welcome">
  <div class="collage">
    <div class="tile tile-a" role="img" aria-label="Pepperoni pizza on a wooden board"></div>
    <div class="tile tile-b" role="img" aria-label="Pizza with basil and tomatoes"></div>
    <div class="tile tile-c" role="img" aria-label="Slices of pizza with chili peppers"></div>
    <div class="tile tile-d" role="img" aria-label="Salami pizza close-up"></div>
  </div>
  <div class="welcome-copy">
    <h2>WELCOME TO BIM-ZEE</h2>
    <p>Lorem Ipsum is simply dummy text of the printing and typesetting industry. Lorem Ipsum has been the industry's standard dummy text ever since the 1500s, when an unknown printer took a galley of type and scrambled it to make a type specimen book. It has survived not only five centuries, but also the leap into electronic typesetting, remaining essentially unchanged.</p>
    <p>when an unknown printer took a galley of type and scrambled it to make a type specimen book. It has survived not only five centuries, but also the leap into electronic typesetting, remaining essentially unchanged.</p>
  </div>
  <a class="btn">Click here</a>
</section>

<section class="fun">
  <h2 class="section-title">FUN STORIES</h2>
  <p class="section-sub">Lorem Ipsum is simply dummy text of the printing and typesetting industry has been the industry</p>

  <article class="card" style="left:98px;top:159px">
    <div class="card-photo" style="background:linear-gradient(135deg,#d8a24a,#b8452b)" role="img" aria-label="Vegetable pizza with peppers"></div>
    <div class="card-meta"><span class="card-title">LOREM IPSUM IS SIMPLY</span><svg width="14" height="12" viewBox="0 0 14 12"><path d="M1 11V6h8V3l4 4-4 4V8H3v3z" fill="#e3262c"/></svg></div>
    <div class="card-foot"><span class="comments"><svg width="11" height="11" viewBox="0 0 11 11"><path d="M5.5 1C2.7 1 1 2.6 1 4.5c0 1 .5 1.9 1.4 2.5L2 10l2.6-1.7c.3 0 .6.1.9.1 2.8 0 4.5-1.6 4.5-3.9S8.3 1 5.5 1z" fill="none" stroke="#e3262c"/></svg>120 Comments</span><span class="stars">★★★★★</span></div>
  </article>
  <article class="card" style="left:356px;top:159px">
    <div class="card-photo" style="background:linear-gradient(135deg,#4a4f5c,#8a5a40)" role="img" aria-label="Friends sharing pizza slices"></div>
    <div class="card-meta"><span class="card-title">LOREM IPSUM IS SIMPLY</span><svg width="14" height="12" viewBox="0 0 14 12"><path d="M1 11V6h8V3l4 4-4 4V8H3v3z" fill="#e3262c"/></svg></div>
    <div class="card-foot"><span class="comments"><svg width="11" height="11" viewBox="0 0 11 11"><path d="M5.5 1C2.7 1 1 2.6 1 4.5c0 1 .5 1.9 1.4 2.5L2 10l2.6-1.7c.3 0 .6.1.9.1 2.8 0 4.5-1.6 4.5-3.9S8.3 1 5.5 1z" fill="none" stroke="#e3262c"/></svg>120 Comments</span><span class="stars">★★★★★</span></div>
  </article>
  <article class="card" style="left:612px;top:159px">
    <div class="card-photo" style="background:linear-gradient(135deg,#9b6a44,#c8532f)" role="img" aria-label="Sliced pizza on a wooden table"></div>
    <div class="card-meta"><span class="card-title">LOREM IPSUM IS SIMPLY</span><svg width="14" height="12" viewBox="0 0 14 12"><path d="M1 11V6h8V3l4 4-4 4V8H3v3z" fill="#e3262c"/></svg></div>
    <div class="card-foot"><span class="comments"><svg width="11" height="11" viewBox="0 0 11 11"><path d="M5.5 1C2.7 1 1 2.6 1 4.5c0 1 .5 1.9 1.4 2.5L2 10l2.6-1.7c.3 0 .6.1.9.1 2.8 0 4.5-1.6 4.5-3.9S8.3 1 5.5 1z" fill="none" stroke="#e3262c"/></svg>120 Comments</span><span class="stars">★★★★★</span></div>
  </article>
  <article class="card" style="left:868px;top:159px">
    <div class="card-photo" style="background:linear-gradient(160deg,#3f8f7e,#d9d2c4 55%,#a8673f)" role="img" aria-label="Chef preparing pizza dough in a kitchen"></div>
    <div class="card-meta"><span class="card-title">LOREM IPSUM IS SIMPLY</span><svg width="14" height="12" viewBox="0 0 14 12"><path d="M1 11V6h8V3l4 4-4 4V8H3v3z" fill="#e3262c"/></svg></div>
    <div class="card-foot"><span class="comments"><svg width="11" height="11" viewBox="0 0 11 11"><path d="M5.5 1C2.7 1 1 2.6 1 4.5c0 1 .5 1.9 1.4 2.5L2 10l2.6-1.7c.3 0 .6.1.9.1 2.8 0 4.5-1.6 4.5-3.9S8.3 1 5.5 1z" fill="none" stroke="#e3262c"/></svg>120 Comments</span><span class="stars">★★★★★</span></div>
  </article>

  <a class="btn center-x">View more</a>
</section>

<section class="menus">
  <div class="menus-photo" role="img" aria-label="Group of friends laughing together at a table"></div>
  <div class="menus-shade"></div>
  <h2 class="section-title">MENUS</h2>
  <p class="menus-text">Lorem Ipsum is simply dummy text of the printing and typesetting industry. Lorem Ipsum has been the industry's standard dummy text ever since the 1500s</p>
  <a class="btn center-x">Download our menus</a>
</section>

<section class="past">
  <h2 class="section-title">PAST STORIES</h2>
  <p class="section-sub">Lorem Ipsum is simply dummy text of the printing and typesetting industry has been the industry</p>

  <article class="card" style="left:98px;top:190px"><div class="card-photo" style="background:linear-gradient(135deg,#8fa3b8,#c27a5a)" role="img" aria-label="Two friends eating pizza outdoors"></div><div class="card-meta"><span class="card-title">LOREM IPSUM IS SIMPLY</span><svg width="14" height="12" viewBox="0 0 14 12"><path d="M1 11V6h8V3l4 4-4 4V8H3v3z" fill="#e3262c"/></svg></div><div class="card-foot"><span class="comments"><svg width="11" height="11" viewBox="0 0 11 11"><path d="M5.5 1C2.7 1 1 2.6 1 4.5c0 1 .5 1.9 1.4 2.5L2 10l2.6-1.7c.3 0 .6.1.9.1 2.8 0 4.5-1.6 4.5-3.9S8.3 1 5.5 1z" fill="none" stroke="#e3262c"/></svg>120 Comments</span><span class="stars">★★★★★</span></div></article>
  <article class="card" style="left:356px;top:190px"><div class="card-photo" style="background:linear-gradient(135deg,#c98a4a,#a5402a)" role="img" aria-label="Pizzas on wooden boards"></div><div class="card-meta"><span class="card-title">LOREM IPSUM IS SIMPLY</span><svg width="14" height="12" viewBox="0 0 14 12"><path d="M1 11V6h8V3l4 4-4 4V8H3v3z" fill="#e3262c"/></svg></div><div class="card-foot"><span class="comments"><svg width="11" height="11" viewBox="0 0 11 11"><path d="M5.5 1C2.7 1 1 2.6 1 4.5c0 1 .5 1.9 1.4 2.5L2 10l2.6-1.7c.3 0 .6.1.9.1 2.8 0 4.5-1.6 4.5-3.9S8.3 1 5.5 1z" fill="none" stroke="#e3262c"/></svg>120 Comments</span><span class="stars">★★★★★</span></div></article>
  <article class="card" style="left:612px;top:190px"><div class="card-photo" style="background:linear-gradient(135deg,#3a3530,#a8713f)" role="img" aria-label="Hands reaching for pizza slices"></div><div class="card-meta"><span class="card-title">LOREM IPSUM IS SIMPLY</span><svg width="14" height="12" viewBox="0 0 14 12"><path d="M1 11V6h8V3l4 4-4 4V8H3v3z" fill="#e3262c"/></svg></div><div class="card-foot"><span class="comments"><svg width="11" height="11" viewBox="0 0 11 11"><path d="M5.5 1C2.7 1 1 2.6 1 4.5c0 1 .5 1.9 1.4 2.5L2 10l2.6-1.7c.3 0 .6.1.9.1 2.8 0 4.5-1.6 4.5-3.9S8.3 1 5.5 1z" fill="none" stroke="#e3262c"/></svg>120 Comments</span><span class="stars">★★★★★</span></div></article>
  <article class="card" style="left:868px;top:190px"><div class="card-photo" style="background:radial-gradient(circle,#b8532e,#2d2a26 70%)" role="img" aria-label="Pizza on a dark table from above"></div><div class="card-meta"><span class="card-title">LOREM IPSUM IS SIMPLY</span><svg width="14" height="12" viewBox="0 0 14 12"><path d="M1 11V6h8V3l4 4-4 4V8H3v3z" fill="#e3262c"/></svg></div><div class="card-foot"><span class="comments"><svg width="11" height="11" viewBox="0 0 11 11"><path d="M5.5 1C2.7 1 1 2.6 1 4.5c0 1 .5 1.9 1.4 2.5L2 10l2.6-1.7c.3 0 .6.1.9.1 2.8 0 4.5-1.6 4.5-3.9S8.3 1 5.5 1z" fill="none" stroke="#e3262c"/></svg>120 Comments</span><span class="stars">★★★★★</span></div></article>

  <article class="card" style="left:98px;top:527px"><div class="card-photo" style="background:linear-gradient(135deg,#7a6a5c,#c49a7a)" role="img" aria-label="Friends taking a group photo"></div><div class="card-meta"><span class="card-title">LOREM IPSUM IS SIMPLY</span><svg width="14" height="12" viewBox="0 0 14 12"><path d="M1 11V6h8V3l4 4-4 4V8H3v3z" fill="#e3262c"/></svg></div><div class="card-foot"><span class="comments"><svg width="11" height="11" viewBox="0 0 11 11"><path d="M5.5 1C2.7 1 1 2.6 1 4.5c0 1 .5 1.9 1.4 2.5L2 10l2.6-1.7c.3 0 .6.1.9.1 2.8 0 4.5-1.6 4.5-3.9S8.3 1 5.5 1z" fill="none" stroke="#e3262c"/></svg>120 Comments</span><span class="stars">★★★★★</span></div></article>
  <article class="card" style="left:356px;top:527px"><div class="card-photo" style="background:linear-gradient(135deg,#e8ddd0,#c48a5a)" role="img" aria-label="Couple eating pizza slices"></div><div class="card-meta"><span class="card-title">LOREM IPSUM IS SIMPLY</span><svg width="14" height="12" viewBox="0 0 14 12"><path d="M1 11V6h8V3l4 4-4 4V8H3v3z" fill="#e3262c"/></svg></div><div class="card-foot"><span class="comments"><svg width="11" height="11" viewBox="0 0 11 11"><path d="M5.5 1C2.7 1 1 2.6 1 4.5c0 1 .5 1.9 1.4 2.5L2 10l2.6-1.7c.3 0 .6.1.9.1 2.8 0 4.5-1.6 4.5-3.9S8.3 1 5.5 1z" fill="none" stroke="#e3262c"/></svg>120 Comments</span><span class="stars">★★★★★</span></div></article>
  <article class="card" style="left:612px;top:527px"><div class="card-photo" style="background:linear-gradient(180deg,#dfe6ea,#e0a050)" role="img" aria-label="Man holding a giant pizza slice"></div><div class="card-meta"><span class="card-title">LOREM IPSUM IS SIMPLY</span><svg width="14" height="12" viewBox="0 0 14 12"><path d="M1 11V6h8V3l4 4-4 4V8H3v3z" fill="#e3262c"/></svg></div><div class="card-foot"><span class="comments"><svg width="11" height="11" viewBox="0 0 11 11"><path d="M5.5 1C2.7 1 1 2.6 1 4.5c0 1 .5 1.9 1.4 2.5L2 10l2.6-1.7c.3 0 .6.1.9.1 2.8 0 4.5-1.6 4.5-3.9S8.3 1 5.5 1z" fill="none" stroke="#e3262c"/></svg>120 Comments</span><span class="stars">★★★★★</span></div></article>
  <article class="card" style="left:868px;top:527px"><div class="card-photo" style="background:linear-gradient(135deg,#5a3a2c,#c23a2a)" role="img" aria-label="Pizza with tomato sauce on a rustic table"></div><div class="card-meta"><span class="card-title">LOREM IPSUM IS SIMPLY</span><svg width="14" height="12" viewBox="0 0 14 12"><path d="M1 11V6h8V3l4 4-4 4V8H3v3z" fill="#e3262c"/></svg></div><div class="card-foot"><span class="comments"><svg width="11" height="11" viewBox="0 0 11 11"><path d="M5.5 1C2.7 1 1 2.6 1 4.5c0 1 .5 1.9 1.4 2.5L2 10l2.6-1.7c.3 0 .6.1.9.1 2.8 0 4.5-1.6 4.5-3.9S8.3 1 5.5 1z" fill="none" stroke="#e3262c"/></svg>120 Comments</span><span class="stars">★★★★★</span></div></article>

  <a class="btn center-x">View more</a>
</section>

<section class="partners" aria-label="Partner badges">
  <div class="partner" style="left:110px;width:219px"><span class="badge" style="width:120px;height:44px;border-radius:22px"></span></div>
  <div class="partner" style="left:366px;width:214px"><span class="badge" style="width:130px;height:56px;border-radius:4px"></span></div>
  <div class="partner" style="left:617px;width:212px"><span class="badge" style="width:64px;height:64px;border-radius:50%;background:#8a3a30"></span></div>
  <div class="partner" style="left:871px;width:214px"><span class="badge" style="width:120px;height:44px;border-radius:22px;background:#2b2b2b"></span></div>
</section>

<footer class="site-footer">
  <div class="footer-name">BIM-ZEE</div>
  <nav class="footer-nav"><a href="#">HOME</a><a href="#">ABOUT US</a><a href="#">BLOG</a><a href="#">FUN STORIES</a><a href="#">CONTACT US</a></nav>
  <p class="copyright">© BIM-ZEE, 2017. ALL RIGHTS RESERVED.</p>
  <div class="social" aria-label="Social links"><span></span><span></span><span></span><span></span><span></span></div>
</footer>

</body>
</html>
```